Business Card Design Project - del varosi group

dear Sirs

we need business card design for our group ( DEL Varosi Group ) , i have got the Logo design of our group from pixel harbor in previous , so all need details relating to our group i think available with you, as well as the the chosen logo design

we hope to provide us with business card logo that to be appropaite and satisfactory to us .

thanks

note : logo design of our group is attached .
Updates

Reason: please extend the deadline of my project for additional 15 days because i didn't received appropriate design for our gruop yet . kindly beaware that i have received 77 design till now , supossed to send me 200-250 design at least . thanks

Target Market(s)

contents

name : Kerem EL Nadiri

position : Operation Manager

Industry/Entity Type

Business

Requirements
Must have

• person name

group logo
Nice to have
• logo color matching with back background

```html
<!DOCTYPE html>
<html lang="en">
<head>
<meta charset="utf-8">
<title>DEL Varosi Group – Business Card</title>
<link rel="stylesheet" href="https://fonts.googleapis.com/css2?family=Open+Sans:wght@400;600&display=swap">
<style>
  :root {
    --page-bg: #f1f1f8;
    --silver-light: #e6e7ea;
    --silver-mid: #c9cbd0;
    --silver-dark: #9fa2a8;
    --brand-blue: #1d5aa6;
    --brand-blue-light: #3f84d4;
    --brand-blue-deep: #154a8c;
    --accent-gold: #e3a524;
    --text-white: #ffffff;
  }
  * { box-sizing: border-box; margin: 0; padding: 0; }
  html, body {
    width: 1200px; height: 900px; overflow: hidden;
    background: var(--page-bg);
    font-family: "Open Sans", sans-serif;
  }
  .canvas {
    width: 1200px; height: 900px;
    display: flex; align-items: center; justify-content: center; gap: 50px;
  }
  .card {
    position: relative;
    width: 540px; height: 310px;
    overflow: hidden;
    box-shadow: 0 10px 24px rgba(40, 50, 80, 0.18);
  }

  /* ---------- Front ---------- */
  .card-front {
    background: linear-gradient(180deg, var(--silver-light) 0%, var(--silver-mid) 45%, var(--silver-light) 70%, var(--silver-dark) 100%);
    border-bottom: 4px solid var(--brand-blue);
  }
  .brand-lockup {
    position: absolute; display: flex; align-items: center; gap: 10px;
    font-weight: 600; text-transform: uppercase; letter-spacing: 1px;
  }
  .brand-square { width: 16px; height: 16px; }
  .card-front .brand-lockup { left: 36px; top: 38px; color: var(--brand-blue); font-size: 24px; }
  .card-front .brand-square { background: var(--brand-blue); }

  .info-band {
    position: absolute; left: 0; right: 0; top: 104px; height: 116px;
    background: linear-gradient(90deg, var(--brand-blue-light) 0%, var(--brand-blue) 55%, var(--brand-blue-deep) 100%);
    border-top: 3px solid var(--brand-blue-deep);
    border-bottom: 3px solid var(--brand-blue-deep);
    display: flex; align-items: center;
  }
  .person {
    width: 290px; text-align: center; color: var(--text-white);
  }
  .person-name { font-size: 21px; font-weight: 400; }
  .person-role { font-size: 13px; color: var(--accent-gold); margin-top: 2px; }
  .band-divider { width: 1px; height: 76px; background: rgba(255,255,255,0.8); }
  .contact-list {
    list-style: none; padding-left: 22px;
    color: var(--text-white); font-size: 11.5px; line-height: 1.6;
  }
  .web-address {
    position: absolute; right: 28px; color: var(--brand-blue); font-size: 13px; font-weight: 600;
  }
  .card-front .web-address { top: 236px; }
  .postal-address {
    position: absolute; left: 36px; bottom: 18px;
    color: var(--brand-blue); font-size: 14px; line-height: 1.35;
  }

  /* ---------- Back ---------- */
  .card-back {
    background: var(--silver-light);
    border-bottom: 4px solid var(--brand-blue);
  }
  .metal-stripe {
    position: absolute; left: 0; right: 0; height: 42px;
    background: linear-gradient(180deg, var(--silver-dark) 0%, var(--silver-light) 50%, var(--silver-mid) 100%);
  }
  .metal-stripe.upper { top: 66px; }
  .metal-stripe.lower { top: 206px; }
  .logo-band {
    position: absolute; left: 0; right: 0; top: 108px; height: 98px;
    background: linear-gradient(90deg, var(--brand-blue-deep) 0%, var(--brand-blue) 50%, var(--brand-blue-deep) 100%);
    display: flex; align-items: center; justify-content: center;
  }
  .card-back .brand-lockup { position: static; color: var(--text-white); font-size: 28px; }
  .card-back .brand-square { background: var(--text-white); }
  .card-back .web-address { bottom: 18px; }
</style>
</head>
<body>
<main class="canvas">

  <section class="card card-front" aria-label="Business card front">
    <div class="brand-lockup"><span class="brand-square"></span>DEL Varosi Group</div>

    <div class="info-band">
      <div class="person">
        <p class="person-name">Kerem EL Nadiri</p>
        <p class="person-role">Operation Manager</p>
      </div>
      <div class="band-divider"></div>
      <ul class="contact-list">
        <li>P : +971 4 555 0142</li>
        <li>M : +971 4 555 0143</li>
        <li>F : +971 4 555 0144</li>
        <li>E : info@delvarosi.com</li>
      </ul>
    </div>

    <p class="web-address">www.delvarosi.com</p>
    <p class="postal-address">P.O. Box: 48210<br>Coral Bay, United Arab Emirates</p>
  </section>

  <section class="card card-back" aria-label="Business card back">
    <div class="metal-stripe upper"></div>
    <div class="logo-band">
      <div class="brand-lockup"><span class="brand-square"></span>DEL Varosi Group</div>
    </div>
    <div class="metal-stripe lower"></div>
    <p class="web-address">www.delvarosi.com</p>
  </section>

</main>
</body>
</html>
```